Wordpress Design Project

Hi,

I would like a more modern colourful design doing for my website ZAP Lnx (www.za%plnx.com - remove percentage). But I do still want to keep the same sort of colors, just maybe lighter. More interesting.

I want the inside pages to NOT all look the same with just boring text.

I want the site to look more appealing and maybe a new logo.
Updates

I would like to mention I would prefer to keep the same logo after rethinking it (possibly a slight refresh of the logo if you feel its a good idea) and the same color scheme as at present.

Saves us rebranding a lot of our apps, tools online ads etc.

Also I thought it is worth mentioning we have 2 parts to the site. The front end and the logged in area. It would be good if when making the front end you keep in mind the back end at http://p.za%plnx.com (remove percentage). We can only edit this limitedly (can edit the entire footer, the logo and full CSS of it). Would be good if we could make sure the header and footer can be used on the back end as well maybe to make it match.

I also want layouts making not just for the homepage. Obviously every page will basically be the same but I don't want all the other pages to just be 'text' and no real layout.

You can see out main pages on the website at the moment, I want those other pages to be laid out nice and differently as well. For example the testimonials page could be more interesting with speech bubbles and pictures of each person (just use placeholders). The affiliates page could be a description and then a nice fancy list of features why to join etc. 

Nothing overly complicated but I think it makes the whole site seem a lot better.

Target Market(s)

Affiliate Marketing. International.

Requirements
Must have
• Needs to be more room for links across the navigation at the top, also sub menus (at present we have a lot of pages which are hidden deep within other pages).
Nice to have
• Lists of features for advertisers and affiliates on the homepage part.

Menu items and buttons have nice hover over effects.

I want to get across on our pages all the different unique features we have.

Maybe some kind of slider which has past offer logos in, just use example logos.

```html
<!DOCTYPE html>
<html lang="en">
<head>
<meta charset="utf-8">
<title>ZAP Lnx – International Affiliate Network</title>
<link href="https://fonts.googleapis.com/css2?family=PT+Sans+Narrow:wght@400;700&family=Source+Sans+3:wght@300;400;600&display=swap" rel="stylesheet">
<style>
:root{
  --blue-dark:#1b68a6;
  --blue-light:#5aa6da;
  --navy:#0d3a5c;
  --ink-blue:#16507f;
  --orange:#f7941d;
  --orange-dark:#ee830d;
  --orange-light:#fcab3f;
  --text:#6b6b6b;
  --line:#dde7ef;
  --hero-top:#d5e6f3;
  --hero-bottom:#f4f9fd;
  --footer-bg:#eef5fb;
  --white:#ffffff;
}
*{box-sizing:border-box;margin:0;padding:0}
html,body{width:997px;height:1200px;overflow:hidden}
body{position:relative;background:var(--white);font-family:"Source Sans 3",Arial,sans-serif;color:var(--text)}
h1,h2,h3{font-weight:400}
.abs{position:absolute}

/* header */
.site-header{left:0;top:0;width:997px;height:105px;background:linear-gradient(180deg,var(--blue-light),var(--blue-dark))}
.brand{left:76px;top:34px;display:flex;align-items:center;gap:10px}
.brand-mark{width:14px;height:14px;background:var(--white);border-radius:50%}
.brand-name{font-family:"Source Sans 3",sans-serif;font-weight:600;font-size:30px;line-height:34px;color:var(--white)}
.callout{right:78px;top:46px;text-align:right;color:var(--white)}
.callout-label{font-size:15px;font-weight:300;color:#cfe3f2}
.callout-phone{font-size:19px;font-weight:400;margin-top:2px}

/* nav */
.main-nav{left:0;top:105px;width:997px;height:43px;background:linear-gradient(180deg,var(--orange-light),var(--orange-dark));border-bottom:1px solid #e07a08}
.main-nav ul{list-style:none;display:flex;align-items:center;height:43px;padding-left:95px}
.main-nav li{font-family:"PT Sans Narrow",sans-serif;font-weight:700;font-size:17.5px;color:var(--white);text-transform:uppercase;display:flex;align-items:center}
.main-nav li+li::before{content:"";display:inline-block;width:1px;height:16px;background:rgba(255,255,255,.5);margin:0 24px}

/* hero */
.hero{left:0;top:148px;width:997px;height:328px;background:linear-gradient(180deg,var(--hero-top),var(--hero-bottom) 80%,#e2eef8)}
.hero-title{left:87px;top:200px;font-family:"PT Sans Narrow",sans-serif;font-weight:700;font-size:32px;color:var(--orange)}
.hero-sub{left:87px;top:238px;font-family:"PT Sans Narrow",sans-serif;font-weight:700;font-size:20px;color:var(--ink-blue)}
.hero-text{left:87px;top:268px;width:350px;font-size:12.5px;line-height:18.5px;font-weight:300;color:var(--blue-dark)}
.btn-join{left:87px;top:334px;width:110px;height:30px;background:var(--ink-blue);color:var(--white);font-family:"PT Sans Narrow",sans-serif;font-weight:700;font-size:15px;display:flex;align-items:center;justify-content:center;border-radius:2px}
.hero-dots{left:88px;top:389px;display:flex;gap:3px}
.hero-dots span{width:9px;height:9px;border-radius:50%;background:var(--ink-blue)}
.hero-dots span:first-child{background:var(--orange)}
.hero-device{left:587px;top:164px;width:284px;height:291px;background:linear-gradient(180deg,#4a4f55,#1a1a1a);border-radius:22px;opacity:.9}

/* welcome */
.welcome-title{left:78px;top:506px;font-size:21.5px;color:#333}
.welcome-copy{left:78px;top:539px;width:548px;font-size:12.6px;line-height:18.5px;font-weight:300}
.welcome-copy p+p{margin-top:12px}
.badges{left:76px;top:663px;display:flex;gap:4px}
.badge{width:120px;height:33px;border:1px solid var(--line);display:flex;align-items:center;gap:5px;padding-left:4px;background:var(--white)}
.badge-icon{width:24px;height:24px;border-radius:50%;background:linear-gradient(135deg,#7fb2df,var(--ink-blue));flex:none}
.badge-icon.square{border-radius:3px;width:20px;background:linear-gradient(180deg,#5d7fa0,#1c3d5c)}
.badge-icon.warm{background:linear-gradient(135deg,#fbb040,#d55a12)}
.badge b{display:block;font-size:10px;font-weight:600;color:var(--blue-dark);line-height:11px}
.badge small{display:block;font-size:6.5px;color:var(--blue-dark);line-height:9px}
.divider{left:648px;top:510px;width:1px;height:150px;background:linear-gradient(180deg,var(--white),#e4ecf3,var(--white))}

/* blog */
.blog-title{left:680px;top:506px;font-size:20px;color:var(--ink-blue)}
.blog-list{left:683px;top:538px;width:225px;list-style:none}
.blog-list li{height:28.5px;border-bottom:1px solid var(--line);display:flex;align-items:center;font-size:12px;color:var(--ink-blue)}
.blog-list li:last-child{border-bottom:none}
.blog-list li::before{content:"";border-left:4px solid var(--ink-blue);border-top:3.5px solid transparent;border-bottom:3.5px solid transparent;margin:0 6px 0 3px}

/* feature boxes */
.panel{top:732px;width:262px;height:312px;border:1px solid #e6edf3;background:var(--white)}
.panel-title{position:absolute;left:23px;top:17px;font-size:19.5px;color:var(--ink-blue)}
.panel-visual{position:absolute;left:19px;top:45px;width:226px;height:95px;border:1px solid var(--line)}
.panel-visual.ad{background:linear-gradient(135deg,#cfe0ee,#f3f1ea 50%,#e8c2c4)}
.panel-visual.net{background:radial-gradient(circle at 50% 50%,#e6eef8,var(--white) 70%)}
.panel-text{position:absolute;left:21px;top:150px;width:216px;font-size:12.2px;line-height:18.5px;font-weight:300;hyphens:auto}
.btn-signup{position:absolute;left:18px;top:253px;width:92px;height:27px;background:linear-gradient(180deg,var(--orange-light),var(--orange-dark));color:var(--white);font-family:"PT Sans Narrow",sans-serif;font-weight:700;font-size:13px;display:flex;align-items:center;justify-content:center}
.login-head{position:absolute;left:-1px;top:-1px;width:262px;height:43px;background:var(--navy);color:var(--white);font-size:19.5px;padding:10px 0 0 26px}
.login-note{position:absolute;left:25px;top:60px;width:222px;font-size:11.5px;line-height:18.5px;color:var(--blue-dark);font-weight:300;hyphens:auto}
.field-label{position:absolute;left:23px;font-size:11.5px;color:var(--ink-blue)}
.field{position:absolute;left:23px;width:207px;height:25px;border:1px solid #c7d9e8}
.forgot{position:absolute;left:24px;top:209px;font-size:10.5px;color:var(--ink-blue)}
.btn-login{position:absolute;left:23px;top:233px;width:61px;height:26px;background:linear-gradient(180deg,var(--orange-light),var(--orange-dark));color:var(--white);font-size:13px;display:flex;align-items:center;justify-content:center}
.signup-link{position:absolute;left:89px;top:237px;font-size:12px;color:var(--orange)}

/* footer */
.site-footer{left:0;top:1078px;width:997px;height:122px;background:var(--footer-bg);border-top:1px solid #cfe0ee}
.footer-links{position:absolute;left:72px;top:34px;display:flex;list-style:none;font-size:11.8px;color:var(--ink-blue);text-transform:uppercase}
.footer-links li+li::before{content:"|";margin:0 7px}
.copyright{position:absolute;left:72px;top:59px;font-size:11px;color:#555}
.social{position:absolute;left:834px;top:31px;display:flex;gap:4px}
.social span{width:23px;height:23px;border-radius:3px;background:linear-gradient(180deg,#6aa8dc,#2f6ea8)}
</style>
</head>
<body>

<header class="site-header abs">
  <div class="brand abs"><span class="brand-mark"></span><span class="brand-name">ZAP Lnx</span></div>
  <div class="callout abs">
    <div class="callout-label">Call Us Now</div>
    <div class="callout-phone">+44 (0) 1632 960418</div>
  </div>
</header>

<nav class="main-nav abs">
  <ul>
    <li>Home</li><li>About Us</li><li>Our Blog</li><li>Testimonials</li><li>Affiliates</li><li>Advertisers</li><li>Contact Us</li>
  </ul>
</nav>

<section class="hero abs"></section>
<h1 class="hero-title abs">International Affiliate Network</h1>
<h2 class="hero-sub abs">Duis tincidunt lectus quis dui viverra</h2>
<p class="hero-text abs">Suspendisse vulputate aliquam dui. Nulla elementum dui ut augue. Aliquam vehicula mi at mauris. Maecenas placerat, nisl at consequat rhoncu</p>
<div class="btn-join abs">Join Us Today</div>
<div class="hero-dots abs"><span></span><span></span><span></span><span></span></div>
<div class="hero-device abs" role="img" aria-label="Two smartphones showing the mobile affiliate dashboard with opportunities list and bar chart"></div>

<h2 class="welcome-title abs">Welcome to the ZAP Lnx Affiliate Network.</h2>
<div class="welcome-copy abs">
  <p>On time payments, hot &amp; exclusive CPL/CPA offers, fast support and low fees for advertisers, is the making of a leading affiliate network! ZAP Lnx offer a wide range of advertisers for your websites. So you can start monetizing your traffic or get an additional revenue stream, today.</p>
  <p>With the ZAP Lnx Affiliate Network we focus on lead generation offers. We have a range of competitions, surveys, incentives and gambling offers. Whatever the industry, you will be able to find offers</p>
</div>
<div class="badges abs">
  <div class="badge"><span class="badge-icon square"></span><div><b>Mobile Stats</b><small>ZAP Lnx Mobile Website</small></div></div>
  <div class="badge"><span class="badge-icon"></span><div><b>Orbit Browser</b><small>Official ZAP Lnx Extension</small></div></div>
  <div class="badge"><span class="badge-icon warm"></span><div><b>Ember Browser</b><small>Official ZAP Lnx Extension</small></div></div>
</div>
<div class="divider abs"></div>

<h2 class="blog-title abs">Recent Blog Post</h2>
<ul class="blog-list abs">
  <li>Mauris vel lacus vitae vestibulum volutpat</li>
  <li>Suspendisse vulputate aliquam dui</li>
  <li>Aliquam vehicula mi at mauris.</li>
  <li>Morbi magna magna tincidunt</li>
</ul>

<section class="panel abs" style="left:76px">
  <h3 class="panel-title">Advertisers</h3>
  <div class="panel-visual ad" role="img" aria-label="Newspaper pages with a red circle around a 'your ad here' space"></div>
  <p class="panel-text">Generate sales/leads to your website instantly with the ZAP Lnx Affiliate Network. Only pay on performance, no monthly or setup fees. ZAP Lnx takes the risk out of advertising</p>
  <div class="btn-signup">SIGN UP NOW</div>
</section>

<section class="panel abs" style="left:364px">
  <h3 class="panel-title">Affilates</h3>
  <div class="panel-visual net" role="img" aria-label="Network of figure groups linked to a central point"></div>
  <p class="panel-text">Get access to a wide range of top performing offers for your websites and email marketing lists. Fresh and exclusive offers to promote. Join over 2,000 affiliates already signed up to ZAP Lnx.</p>
  <div class="btn-signup">SIGN UP NOW</div>
</section>

<section class="panel abs" style="left:652px">
  <h3 class="login-head">Account Login</h3>
  <p class="login-note">Nunc tempus felis vitae urna. Vivamus porttitor, g, purus nisi eleifend</p>
  <label class="field-label" style="top:103px">Email address</label>
  <div class="field" style="top:123px"></div>
  <label class="field-label" style="top:158px">Password</label>
  <div class="field" style="top:178px"></div>
  <span class="forgot">Forgot Password ?</span>
  <div class="btn-login">Login</div>
  <span class="signup-link">or Sign up</span>
</section>

<footer class="site-footer abs">
  <ul class="footer-links">
    <li>Affiliate Terms &amp; Conditions</li><li>Advertiser Terms &amp; Conditions</li><li>Privacy Policy &amp; Cookies</li><li>FAQ</li><li>Contact Us</li>
  </ul>
  <p class="copyright">© 2013 Zapline Media UK Ltd - All Rights Reserved.</p>
  <div class="social"><span></span><span></span><span></span></div>
</footer>

</body>
</html>
```